eBook-Cover für Thriller gesucht
An dieser Stelle ein großes Lob und vielen Dank an die Designerin Larosa. Auch das zweite Buchcover ist wieder überaus gelungen, eine ganz tolle Arbeit. Auch die angenehme Zusammenarbeit war mir, wie schon beim ersten Auftrag, eine Freude. Ebenso hervorzuheben ist die Schnelligkeit und Kreativität, mit der die Designerin auf Änderungswünsche reagiert. Als Auftraggeber gebe ich verdiente fünf Sterne und bin mit dem Ergebnis wirklich sehr zufrieden.
Zielgruppe
Ich bin Autor. Zielgruppe sind (anspruchsvolle) Leser/innen von Thrillern und Kriminalromanen im ebook-Bereich.
Aufgabenstellung
- Gesucht wird ein ebook-Cover für einen Thriller mit dem Titel 'Kaltgrund'
- Grobe Aufteilung siehe Skizzen
- Fokus des Covers liegt auf dem Buchtitel und dem Motiv ('Blauer Drachen')
- Hintergrund eher hell, Assoziation mit zarter Eisfläche mit angedeuteten Rissen vom Hauptmotiv ausgehend. Dadurch auch Tiefe und Dreidimensionalität. (Beispiel zum Hintergrund: 'Schattenfrist' von Heinrich Wendel, jedoch ohne Blut )
-Titelschrift groß, Stil 'gekratzt' bzw. 'gestrichelt', (Schriftart ähnlich wie Autorenname bei 'Die Schleuse' von Matthias Kolbe). Schrift groß und 'treppenförmig' neben dem Hauptmotiv angeordnet. Schriftfarbe schwarz/dunkelblau, ähnlich Hauptmotiv (Bsp.: 'Schwarzeid' von Heinrich Wendel)
Hauptmotiv ist der vom rechten Coverrand hineinragende 'Blaue Drachen' (Glaucus atlanticus, siehe hochgeladenes Beispielbild von Wissnetz)
- Schriftart von Autorenname und Genre eher klar
- eigene Detailvorschläge zur Optimierung des Ergebnisses möglich bzw. erwünscht

```html
<!DOCTYPE html>
<html lang="de">
<head>
<meta charset="utf-8">
<title>Kaltgrund – Thriller</title>
<link rel="stylesheet" href="https://fonts.googleapis.com/css2?family=Oswald:wght@400&family=Cabin+Sketch:wght@700&display=swap">
<style>
  :root {
    --ice-light: #eef4f9;
    --ice-mid: #b9d0e2;
    --ice-deep: #7fa3c2;
    --ink: #111418;
    --title-blue: #1f2f78;
    --dragon-blue: #3b4fa0;
    --dragon-pale: #c9d3ea;
  }
  html, body {
    margin: 0;
    padding: 0;
    width: 750px;
    height: 1200px;
    overflow: hidden;
    background: var(--ice-light);
  }
  .cover {
    position: relative;
    width: 750px;
    height: 1200px;
    overflow: hidden;
  }
  .ice-surface {
    position: absolute;
    inset: 0;
    background:
      radial-gradient(ellipse 60% 40% at 70% 35%, rgba(255,255,255,0.75), transparent 70%),
      radial-gradient(ellipse 70% 35% at 30% 95%, var(--ice-deep), transparent 75%),
      linear-gradient(170deg, var(--ice-light) 0%, var(--ice-mid) 55%, var(--ice-deep) 100%);
  }
  .blue-dragon {
    position: absolute;
    left: 300px;
    top: 235px;
    width: 470px;
    height: 420px;
    background:
      radial-gradient(ellipse 18% 45% at 62% 48%, var(--dragon-blue), transparent 75%),
      radial-gradient(ellipse 48% 38% at 55% 45%, rgba(59,79,160,0.55), transparent 72%),
      radial-gradient(ellipse 60% 50% at 55% 45%, rgba(201,211,234,0.5), transparent 80%);
  }
  .author {
    position: absolute;
    top: 22px;
    left: 0;
    width: 100%;
    margin: 0;
    text-align: center;
    font-family: "Oswald", sans-serif;
    font-weight: 400;
    font-size: 66px;
    letter-spacing: 4px;
    color: var(--ink);
  }
  .title {
    margin: 0;
    font-family: "Cabin Sketch", cursive;
    font-weight: 700;
    color: var(--title-blue);
    font-size: 170px;
    line-height: 1;
  }
  .title-line {
    position: absolute;
    display: block;
    letter-spacing: 2px;
  }
  .title-line--first  { left: 32px;  top: 450px; }
  .title-line--second { left: 290px; top: 585px; }
  .title-line--third  { left: 480px; top: 715px; }
  .genre {
    position: absolute;
    bottom: 38px;
    left: 0;
    width: 100%;
    margin: 0;
    text-align: center;
    font-family: "Oswald", sans-serif;
    font-weight: 400;
    font-size: 40px;
    letter-spacing: 3px;
    color: var(--ink);
  }
</style>
</head>
<body>
  <main class="cover">
    <div class="ice-surface" role="img" aria-label="Helle, zart gerissene Eisfläche in Blau- und Weißtönen"></div>
    <div class="blue-dragon" role="img" aria-label="Blauer Drachen (Glaucus atlanticus), der vom rechten Rand ins Bild ragt"></div>
    <p class="author">JONAS FELDMARK</p>
    <h1 class="title" aria-label="Kaltgrund">
      <span class="title-line title-line--first">KALT</span>
      <span class="title-line title-line--second">GRU</span>
      <span class="title-line title-line--third">ND</span>
    </h1>
    <p class="genre">THRILLER</p>
  </main>
</body>
</html>
```